POS Systems

Redesign existing site with improvement in layout an sitemap

I need Responsive PSD Designs

Current site is http://vantelpoint.com.au/

Client is no longer selling Cash Registers

Only doing Touch Screen Point of Sale Systems
for 4 main industries (Restaurants and Cafes, Grocery and Convenience, Fruit & Veg, Bars, Pubs and Clubs)

Sitemap:

1. Home - With 4 types of businesses serviced, 4 Video Testimonials, End Of Financial Year Sale, Finance Options

2. Our System - Video, text, Boxes of 4 Different Industries, Book a Consultation / Call
Drop down menu for each different industry

(Restaurants and Cafes, Grocery and Convenience, Fruit & Veg, Bars, Pubs and Clubs)

3. About Us - text about history

4. Events

5. Testimonials

6. News - blog page

7. Gallery

8. Contact

#I need PSD Files and I will convert to Wordpress Myself

#I need the Each page designed please except Gallery

# I will build the site on Wordpress

# Designs will need to include responsiveness

Target Market(s)

Business Owners who want to upgrade to a POS System to increase productivity

Industry/Entity Type

Industry

Requirements
Must have
• Menu as above
Responsive Design

```html
<!DOCTYPE html>
<html lang="en">
<head>
<meta charset="utf-8">
<title>VantelPoint – Touch Screen Point of Sale Systems</title>
<link rel="stylesheet" href="https://fonts.googleapis.com/css2?family=Open+Sans:wght@400;600;700&display=swap">
<style>
:root{
  --navy:#34449a;
  --band-top:#2f3f8f;
  --band:#3c4c9e;
  --band-dark:#33428f;
  --green:#6bbd3f;
  --green-light:#8fd05e;
  --green-dark:#4e9e2a;
  --text:#555a60;
  --muted:#6c7076;
  --heading:#3a3d42;
  --line:#dcdcdc;
  --footer:#f2f2f2;
}
*{margin:0;padding:0;box-sizing:border-box}
html,body{width:1142px;height:1200px;overflow:hidden;background:#fff}
body{position:relative;font-family:"Open Sans",Arial,sans-serif;color:var(--text)}
.abs{position:absolute}

.header-band{left:0;top:0;width:1142px;height:338px;background:linear-gradient(180deg,var(--band) 0%,var(--band-dark) 100%);border-top:4px solid var(--band-top)}
.brand{left:118px;top:30px;color:#fff}
.brand-name{font-size:34px;font-weight:600;letter-spacing:.5px;line-height:40px;display:flex;align-items:center;gap:8px}
.brand-name .dot{width:12px;height:12px;border-radius:50%;background:var(--green-light)}
.brand-tag{font-size:14px;line-height:20px;margin-top:6px}
.support{right:114px;top:52px;text-align:right;color:#fff}
.support-label{font-size:17px;line-height:22px}
.support-phone{font-size:25px;line-height:32px}

.main-nav{left:108px;top:119px;width:926px;height:47px;display:flex;background:linear-gradient(180deg,var(--green-light),var(--green));border-radius:4px 4px 0 0;overflow:hidden}
.main-nav a{display:flex;align-items:center;justify-content:center;color:#fff;text-decoration:none;font-size:14.5px;height:100%;border-right:1px solid rgba(255,255,255,.25)}
.main-nav a:last-child{border-right:0}
.main-nav a.active{background:linear-gradient(180deg,var(--green),var(--green-dark))}

.hero{left:108px;top:166px;width:926px;height:340px;background:linear-gradient(180deg,#fff 55%,#f4f4ef 100%);border:1px solid var(--line);border-top:0;border-radius:0 0 4px 4px}
.hero-title{left:172px;top:252px;font-weight:700;font-size:29px;line-height:39px}
.hero-title .l1{color:var(--green)}
.hero-title .l2{color:var(--navy);font-size:33px}
.hero-text{left:175px;top:332px;width:340px;font-size:12px;line-height:22px;color:var(--muted)}
.hero-dots{left:177px;top:386px;display:flex;gap:3px}
.hero-dots span{width:11px;height:11px;border-radius:50%;background:#5d5f63}
.hero-device{left:640px;top:184px;width:276px;height:302px;border-radius:14px;background:linear-gradient(160deg,#3a3c40,#15161a)}

.welcome-title{left:116px;top:536px;font-size:22px;font-weight:600;color:var(--navy)}
.welcome-lead{left:116px;top:571px;width:580px;font-size:14.5px;line-height:20px;color:var(--text)}
.welcome-body{left:116px;top:622px;width:580px;font-size:11.5px;line-height:21.6px;color:var(--muted)}

.industries-title{left:114px;top:760px;font-size:18px;font-weight:600;color:var(--heading)}
.industry-img{width:133px;height:98px}
.industry-name{font-size:14px;line-height:18px;color:var(--heading);font-weight:600;width:140px}
.industry-text{font-size:11.5px;line-height:18px;color:var(--muted);width:130px;margin-top:2px}

.side-title{font-size:22px;font-weight:600}
.testimonials-title{left:718px;top:536px;color:var(--green)}
.video{left:720px;top:569px;width:307px;height:189px;background:linear-gradient(90deg,#8f938a 0%,#6f6a60 55%,#8b6b55 100%)}
.blog-title{left:720px;top:777px;color:var(--navy)}
.blog-post{left:721px;width:300px}
.blog-post h3{font-size:13.5px;font-weight:600;color:var(--navy);line-height:18px}
.blog-post p{font-size:11.5px;line-height:16.5px;color:var(--muted);margin-top:4px}

.footer{left:0;top:1092px;width:1142px;height:108px;background:var(--footer);border-top:1px solid var(--line)}
.footer-nav{left:112px;top:1119px;font-size:14px;color:#4b4e53;word-spacing:2px}
.footer-nav span{margin:0 7px;color:#6a6d72}
.copyright{left:112px;top:1146px;font-size:11px;color:#6a6d72}
.social{left:915px;top:1122px;display:flex;gap:7px}
.social span{width:22px;height:22px;border-radius:2px;background:#8a92b8}
</style>
</head>
<body>

<div class="abs header-band"></div>

<div class="abs brand">
  <div class="brand-name"><span>VANTELPOINT</span><span class="dot"></span></div>
  <div class="brand-tag">Vantel Point of Sale Solutions</div>
</div>

<div class="abs support">
  <div class="support-label">For Support</div>
  <div class="support-phone">1300 555 019</div>
</div>

<nav class="abs main-nav">
  <a class="active" style="width:95px">HOME</a>
  <a style="width:138px">OUR SYSTEM</a>
  <a style="width:120px">ABOUT US</a>
  <a style="width:101px">EVENTS</a>
  <a style="width:154px">TESTIMONIALS</a>
  <a style="width:85px">BLOG</a>
  <a style="width:112px">G ALLERY</a>
  <a style="width:121px">CONTACT</a>
</nav>

<section class="abs hero"></section>
<h1 class="abs hero-title"><span class="l1">TOUCH SCREEN POINT</span><br><span class="l2">OF SALE SYSTEMS</span></h1>
<p class="abs hero-text">lectus feugiat felis Morbi diam mauris viverra in gravida eu mattis in ante Morbi eget arcu Morbi porta libero</p>
<div class="abs hero-dots"><span></span><span></span><span></span><span></span></div>
<div class="abs hero-device" role="img" aria-label="Touch screen point of sale terminal on a stand"></div>

<h2 class="abs welcome-title">WELCOME TO VANTELPOINT WEBSITE</h2>
<p class="abs welcome-lead">Phasellus felis dolor scelerisque a tempus eget lobortis id libero Aliquam nec erat at purus cursus interdum Vestibulum ligula augue bibendum accumsan vestibulum</p>
<p class="abs welcome-body">Nunc tempus felis vitae urna Vivamus porttitor g purus nisi eleifend libero a tempus libero lectus feugiat felis Morbi diam mauris viverra in gravida eu mattis in ante Morbi eget arcu Morbi porta libero id ullamcorper non-ummy nibh ligula pulvinar metus eget consectetuer augue nisi quis lacus Ut ac mi quis lacus mollis aliquam Curabitur iaculis tempus eros Curabitur vel mi sit amet magna malesuada ultrices</p>

<h2 class="abs industries-title">INDUSTRIES WE WORK</h2>

<div class="abs industry-img" style="left:114px;top:802px;background:linear-gradient(135deg,#5a3528,#a0684a 60%,#3e2a22)" role="img" aria-label="Restaurant owner standing in a cafe"></div>
<div class="abs" style="left:259px;top:799px">
  <div class="industry-name">Restaurants<br>and Cafes</div>
  <div class="industry-text">Vivamus porttitor &nbsp;purus nisi eleifend libero a tempus libero lectus</div>
</div>

<div class="abs industry-img" style="left:416px;top:802px;background:linear-gradient(135deg,#d9d4c8,#b7ad98 50%,#e6e1d6)" role="img" aria-label="Shopper with a trolley in a grocery aisle"></div>
<div class="abs" style="left:562px;top:799px">
  <div class="industry-name">Grocery and<br>Convenience</div>
  <div class="industry-text">Vivamus porttitor &nbsp;purus nisi eleifend libero a tempus libero lectus</div>
</div>

<div class="abs industry-img" style="left:114px;top:932px;background:linear-gradient(135deg,#3f8fb0,#8bb43c 45%,#e0a028 75%,#c2402a)" role="img" aria-label="Fruit and vegetable display shelves"></div>
<div class="abs" style="left:259px;top:929px">
  <div class="industry-name">Fruit &amp; Veg, Bars</div>
  <div class="industry-text">Mauris vel lacus vitae felis vestibulum volutpat Etiam est nunc venenatis tristique</div>
</div>

<div class="abs industry-img" style="left:416px;top:932px;background:linear-gradient(135deg,#3a1a14,#8c3a22 50%,#2a1612)" role="img" aria-label="Dimly lit bar tables set with glasses"></div>
<div class="abs" style="left:562px;top:929px">
  <div class="industry-name">Pubs and Clubs</div>
  <div class="industry-text">Mauris vel lacus vitae felis vestibulum volutpat Etiam est nunc venenatis tristique</div>
</div>

<h2 class="abs side-title testimonials-title">TESTIMONIALS</h2>
<div class="abs video" role="img" aria-label="Video testimonial from a shop owner at his store entrance"></div>
<svg class="abs" style="left:720px;top:569px" width="307" height="189" viewBox="0 0 307 189" aria-hidden="true">
  <path d="M0 70 a23 23 0 0 1 0 46 z" fill="#fff"/>
  <path d="M14 84 l-6 9 6 9" fill="none" stroke="#333" stroke-width="2"/>
  <path d="M307 70 a23 23 0 0 0 0 46 z" fill="#fff"/>
  <path d="M293 84 l6 9 -6 9" fill="none" stroke="#333" stroke-width="2"/>
  <circle cx="153" cy="94" r="17" fill="#1d1d1d" stroke="#fff" stroke-width="3"/>
  <path d="M148 86 l12 8 -12 8z" fill="#fff"/>
</svg>

<h2 class="abs side-title blog-title">RECENT BLOG</h2>
<article class="abs blog-post" style="top:813px">
  <h3>Phasellus felis dolor</h3>
  <p>Vivamus porttitor purus nisi eleifend libero, a tempus libero lectus feugiat felis Morbi diam mauris</p>
</article>
<article class="abs blog-post" style="top:884px">
  <h3>Scelerisque tempus</h3>
  <p>Vivamus porttitor purus nisi eleifend libero, a tempus libero lectus feugiat felis Morbi</p>
</article>
<article class="abs blog-post" style="top:958px">
  <h3>Donec scelerisque leo</h3>
  <p>Nulla sit amet diam Duis non nunc libero a tempus libero lectus feugiat felis Morbi diam mauris viverra in gravida eu mattis Morbi ornare gravida elit l</p>
</article>

<footer class="abs footer"></footer>
<nav class="abs footer-nav">HOME<span>|</span>OUR SYSTEM<span>|</span>ABOUT US<span>|</span>EVENTS<span>|</span>TESTIMONIALS<span>|</span>BLOG<span>|</span>GALLERY<span>|</span>CONTACT</nav>
<p class="abs copyright">© 2014 Company Name. &nbsp;All right reserved. &nbsp;Term of Use</p>
<div class="abs social" aria-label="Social links"><span></span><span></span><span></span><span></span></div>

</body>
</html>
```